A website where experts collaborate on your project

I am building a new website where experts (yes, like designers) collaborate on projects with the project owner. More minds = more collaboration = better end product. Please see Pelmora(dot)com for a quick landing page I created for collaborating on presentations (although there will be many project types offered)

I am looking for a DESIGNER LONG TERM, but for now, just need initial mock ups to show the web programmers.

I have 21 Word documents loosely designed, what I would like to see here is a theme. Please DO NOT GO OFF WHAT YOU CURRENTLY SEE AT PELMORA. What is up now is only a quick landing page.

You can view a Word doc of the homepage here:
https://www.filevanta.com/s/qx83kdm2/home.docx?dl=0

WHAT AM I LOOKING FOR?
A clean, well designed theme.

Here is a link to the logo:
https://www.filevanta.com/s/mr47tpz9/logo%20-%20horizontal.tif?dl=0
-----------------------------------------
Here are a few sites I like the design of and what I like about them:
www.quenbrook.com-all around my favorite, beautiful graphics, clean layout, bold use of colors on a dark background
Ravelto.com- clean layout, The use of humans and bubble style elements.
Mintharbor.com :) clean, bold, unique pop art style but professional
plumevault.com - From the unique colors and artwork and the ability of that art to not interfere with the important elements of the site
sparkwidgets.com-clean, nice colors, well organized and separated sections.
www.dunmereco.com-love the font, use of colors and sectionalized style

All in all, I am not picky and open to so many styles. I would ultimately like the designer I pick to design all 21 pages.
Updates

Hello everyone,Moving forward, I would like you all to pay special attention to the section in my brief titled "Here are a few sites I like the design of and what I like about them". Please see below, I handpicked each one of these as sites I really like. Thank you.Here are a few sites I like the design of and what I like about them:Ravelto.com- clean layout, The use of humans and bubble style elements.Mintharbor.com :) clean, bold, unique pop art style but professionalwriteraccess.com - From the unique colors and artwork and the ability of that art to not interfere with the important elements of the sitegrowthgeeks.com-clean, nice colors, well organized and separated sections.www.dunmereco.com-love the font, use of colors and sectionalized stylewww.quenbrook.com-beautiful graphics, clean layout, bold use of colors----------------------------------------- Added Tuesday, November 24, 2015

I updated the homepage, you can see it here:https://www.dropbox.com/s/kwlkbsookq3cg2m/1new%20homepage.docx?dl=0I am modeling it after my favorite designed site: triplelift.comI love the dark colors with the orange glowing style boldness of the buttons. It's real clean too. Added Tuesday, November 24, 2015

Target Market(s)

small business owners, marketers, freelancer writers, graphic designers,

Industry/Entity Type

Building

Number of Pages Required

5+ page

Requirements
Must have
• I can't think of anything the project must have.
Nice to have
• WHAT AM I LOOKING FOR?
• A clean, well designed theme. I had a designer do a bit of work putting elements together, I found it to be very plain, but I like the Application Page (https://www.filevanta.com/s/jb19ckr3/Pelmora-Website.ai?dl=0)
• Here is a link to the logo:
• https://www.filevanta.com/s/mr47tpz9/logo%20-%20horizontal.tif?dl=0
• Here are a few sites I like the design of and what I like about them:
• Ravelto.com- clean layout, The use of humans and bubble style elements.
• Mintharbor.com :) clean, bold, unique pop art style but professional
• plumevault.com - From the unique colors and artwork and the ability of that art to not interfere with the important elements of the site
• sparkwidgets.com-clean, nice colors, well organized and separated sections.
• www.dunmereco.com-love the font, use of colors and sectionalized style
• www.quenbrook.com-beautiful graphics, clean layout, bold use of colors
• -----------------------------------------
Should not have
• out of the boxed, templated style website. I want this site to be memorable and not look like a thousand others

```html
<!DOCTYPE html>
<html lang="en">
<head>
<meta charset="utf-8">
<title>Pelmora – Experts collaborating on your project</title>
<link rel="stylesheet" href="https://fonts.googleapis.com/css2?family=Open+Sans:ital,wght@0,400;0,600;0,700;1,400&family=Raleway:wght@500;700&display=swap">
<style>
:root{
  --orange:#f29222;
  --orange-dark:#e07d12;
  --orange-light:#f7a53a;
  --blue:#52a5bf;
  --blue-dark:#3f91ab;
  --text:#444;
  --muted:#777;
  --line:#e6e6e6;
  --band:#f4f4f4;
  --white:#fff;
}
*{box-sizing:border-box;margin:0;padding:0}
html,body{width:912px;height:1200px;overflow:hidden;background:var(--white);font-family:"Open Sans",sans-serif;color:var(--text)}
.page{position:relative;width:912px;height:1200px}
.abs{position:absolute}

/* header */
.brand{left:76px;top:38px;display:flex;align-items:center;gap:8px}
.brand-name{font-family:"Open Sans",sans-serif;font-weight:700;font-size:20px;color:var(--orange)}
.brand-dot{width:46px;height:46px;border-radius:50%;background:var(--orange);margin-top:-22px}
.notice{left:393px;top:36px;width:370px;font-size:8.6px;line-height:16px;color:var(--orange)}
.notice span{color:var(--blue)}

/* nav */
.navbar{left:0;top:94px;width:912px;height:38px;background:linear-gradient(var(--orange-light),var(--orange-dark))}
.browse{left:76px;top:100px;width:203px;height:24px;border:1px solid #fbd3a3;border-radius:2px;color:#fff;font-size:9.5px;line-height:22px;padding-left:10px}
.browse::after{content:"";position:absolute;right:0;top:0;width:29px;height:22px;border-left:1px solid #fbd3a3}
.browse .chev{position:absolute;right:11px;top:8px;width:5px;height:5px;border-right:1.3px solid #fff;border-bottom:1.3px solid #fff;transform:rotate(45deg)}
.menu{left:341px;top:94px;display:flex;height:38px}
.menu a{display:block;height:38px;line-height:38px;text-align:center;color:#fff;font-size:9.5px;text-decoration:none;border-right:1px solid rgba(0,0,0,.08)}
.menu a.active{background:var(--blue)}

/* hero */
.hero{left:0;top:132px;width:912px;height:356px;background:linear-gradient(120deg,#6b5443 0%,#8a7258 35%,#4b4a4c 60%,#7d6a57 100%)}
.hero-shade{left:0;top:132px;width:912px;height:356px;background:linear-gradient(90deg,rgba(0,0,0,.35),rgba(0,0,0,0) 60%)}
.hero-title{left:76px;top:250px;font-family:"Raleway",sans-serif;font-weight:700;font-size:24px;color:#fff}
.hero-sub{left:77px;top:281px;width:280px;font-size:12.5px;line-height:23px;color:#fff;font-weight:300}
.hero-btn{left:77px;top:332px;width:106px;height:32px;background:var(--orange);color:#fff;font-size:9px;line-height:32px;text-align:center}
.hero-arrow{top:278px;width:28px;height:28px;border-radius:50%;background:rgba(0,0,0,.3)}
.hero-arrow::after{content:"";position:absolute;top:10px;width:7px;height:7px;border-left:1.5px solid #fff;border-bottom:1.5px solid #fff}
.hero-arrow.prev{left:28px}.hero-arrow.prev::after{left:11px;transform:rotate(45deg)}
.hero-arrow.next{left:860px}.hero-arrow.next::after{left:8px;transform:rotate(-135deg)}

/* panels */
.panel{border:1px solid var(--line);background:#fff}
.panel-head{height:34px;background:linear-gradient(var(--orange-light),var(--orange-dark));color:#fff;font-size:14px;font-weight:400;line-height:34px;padding-left:17px;position:relative}
.filters{left:75px;top:519px;width:217px;height:324px}
.slider{position:relative;height:66px;border-bottom:1px solid var(--line)}
.slider .track{position:absolute;left:24px;top:56px;width:178px;height:3px;background:#eee;top:25px}
.slider .fill{position:absolute;left:24px;top:25px;width:79px;height:3px;background:var(--blue)}
.slider .knob{position:absolute;top:20px;width:12px;height:12px;border-radius:50%;background:var(--blue);border:2px solid #cde6ee}
.slider .lbl{position:absolute;top:41px;font-size:9.5px;color:var(--muted)}
.filter-list{list-style:none}
.filter-list li{height:27px;border-bottom:1px solid var(--line);display:flex;align-items:center;font-size:9.5px;color:#555;position:relative}
.filter-list .ico{width:8px;height:8px;background:#555;margin:0 20px 0 21px;border-radius:1px}
.filter-list .ico.round{border-radius:50%}
.filter-list li::after{content:"";position:absolute;right:28px;top:11px;width:4px;height:4px;border-right:1px solid #666;border-top:1px solid #666;transform:rotate(45deg)}
.save{position:absolute;left:0;bottom:0;width:215px;height:24px;background:var(--blue);color:#fff;font-size:11px;text-align:center;line-height:24px}
.funnel{position:absolute;right:14px;top:13px}

.projects{left:313px;top:519px;width:520px;height:324px;overflow:hidden}
.sort{position:absolute;right:26px;top:0;font-size:9.5px}
.sort u{text-decoration:underline}
.project{position:relative;height:88px;border-bottom:1px solid var(--line)}
.project.alt{background:#f7f7f7}
.avatar{position:absolute;left:21px;width:58px;height:58px;border-radius:50%;background:linear-gradient(#dfe3e6,#9aa4ad);border:1px solid #ddd}
.project .desc{position:absolute;left:102px;font-size:8.5px;color:#555}
.project .meta{position:absolute;left:102px;font-size:10px;color:#555}
.project .meta b{color:var(--blue);font-weight:600;margin-right:9px}
.view{position:absolute;left:392px;width:81px;height:27px;border:1px solid var(--blue);color:var(--blue);font-size:9.5px;text-align:center;line-height:25px;border-radius:2px;background:#fff}
.scroll{position:absolute;right:0;top:34px;width:10px;height:290px;border-left:1px solid var(--line);background:#fafafa}
.scroll i{position:absolute;left:1px;top:45px;width:7px;height:28px;border:1px solid #ccc;background:#eee}

/* testimonials */
.band{left:0;top:880px;width:912px;height:248px;background:var(--band);border-top:1px solid var(--line)}
.t-title{left:0;top:918px;width:912px;text-align:center;font-family:"Raleway",sans-serif;font-weight:700;font-size:23px;color:#333}
.t-photo{left:137px;top:959px;width:108px;height:98px;border-radius:50%;background:linear-gradient(#f2f2f2,#b8bcc0);border:1px solid #ddd}
.t-quote{left:341px;top:970px;width:416px;font-size:9.3px;line-height:18.5px;font-style:italic;color:#666}
.q-mark{font-family:Georgia,serif;font-size:26px;color:#bbb}
.t-name{left:341px;top:1068px;font-size:9.5px;font-weight:700;color:var(--orange)}
.t-role{left:341px;top:1084px;font-size:8.5px;color:#444}
.t-nav{top:1062px;width:9px;height:9px;border-radius:50%;background:#aaa}

/* footer */
.footer{left:0;top:1128px;width:912px;height:72px;background:linear-gradient(var(--orange-light),var(--orange))}
.f-links{left:76px;top:1147px;font-size:9.5px;color:#fff;word-spacing:2px}
.f-copy{left:74px;top:1167px;font-size:9.5px;color:#fff}
.social{left:682px;top:1153px;display:flex;gap:8px}
.social i{width:25px;height:25px;border-radius:50%;display:block;background:rgba(255,255,255,.35);border:1.5px solid rgba(255,255,255,.7)}
</style>
</head>
<body>
<div class="page">

  <div class="abs brand"><span class="brand-name">pelmora</span><span class="brand-dot"></span></div>
  <p class="abs notice">Notification feed-New items <span>in the feeds are highlighted in blue,and they stay highlighted until cleared. You can clear highlights individually or clear them all at once.</span></p>

  <div class="abs navbar"></div>
  <div class="abs browse">Browse<span class="chev"></span></div>
  <nav class="abs menu">
    <a class="active" style="width:86px">Home</a>
    <a style="width:104px">Projects</a>
    <a style="width:110px">How it works</a>
    <a style="width:86px">Plans</a>
    <a style="width:109px">My Account</a>
  </nav>

  <div class="abs hero" role="img" aria-label="Desk scene with a laptop showing the site, notebooks, glasses and stationery"></div>
  <div class="abs hero-shade"></div>
  <h1 class="abs hero-title">Convert more customers</h1>
  <p class="abs hero-sub">Experience the power of experts collaborating on your project.</p>
  <div class="abs hero-btn">Get Started</div>
  <div class="abs hero-arrow prev"></div>
  <div class="abs hero-arrow next"></div>

  <section class="abs panel filters">
    <div class="panel-head">Filters
      <svg class="funnel" width="9" height="9" viewBox="0 0 10 10"><path d="M0 0h10L6 5v5L4 8.5V5z" fill="#fff"/></svg>
    </div>
    <div class="slider">
      <span class="track"></span><span class="fill"></span>
      <span class="knob" style="left:18px"></span><span class="knob" style="left:97px"></span>
      <span class="lbl" style="left:20px">$20</span><span class="lbl" style="left:174px">$1000</span>
    </div>
    <ul class="filter-list">
      <li><span class="ico round"></span>Country</li>
      <li><span class="ico"></span>Categories</li>
      <li><span class="ico round"></span>Time Left</li>
      <li><span class="ico"></span>Active | Expired</li>
      <li><span class="ico"></span>Contains adult content</li>
      <li><span class="ico"></span>keywords</li>
      <li><span class="ico round"></span>followers</li>
    </ul>
    <div class="save">Save Filters</div>
  </section>

  <section class="abs panel projects">
    <div class="panel-head">Crowd Projects
      <span class="sort">Sort: <u>Price</u> | Country | Time left</span>
    </div>
    <div class="project">
      <div class="avatar" style="top:14px" role="img" aria-label="Expert portrait"></div>
      <p class="desc" style="top:37px">Morbi in ante arcu. Maecenas sit amet sem vel</p>
      <p class="meta" style="top:53px"><b>$80</b>U.S time 6days</p>
      <div class="view" style="top:31px">View more</div>
    </div>
    <div class="project alt">
      <div class="avatar" style="top:16px" role="img" aria-label="Expert portrait"></div>
      <p class="desc" style="top:37px">Lorem ipsum dolor sit amet, consectetur adipiscing</p>
      <p class="meta" style="top:53px"><b>$80</b>U.S time 6days</p>
      <div class="view" style="top:29px">View more</div>
    </div>
    <div class="project" style="border:0">
      <div class="avatar" style="top:27px" role="img" aria-label="Expert portrait"></div>
      <p class="desc" style="top:48px">Morbi in ante arcu. Maecenas sit amet sem vel</p>
      <p class="meta" style="top:64px"><b>$80</b>U.S time 6days</p>
      <div class="view" style="top:40px">View more</div>
    </div>
    <div class="scroll"><i></i></div>
  </section>

  <div class="abs band"></div>
  <h2 class="abs t-title">Testimonials</h2>
  <div class="abs t-photo" role="img" aria-label="Portrait of a smiling client in a suit"></div>
  <span class="abs q-mark" style="left:316px;top:955px">“</span>
  <span class="abs q-mark" style="left:778px;top:1005px">”</span>
  <p class="abs t-quote">With Pelmora I have multiple experts perfecting my content and I only pay for the feedback I find valuable. It’s perfect” Dale Fenwick, CEO, Ledger 52| “Before you put any content in front of your audience, crowdsource it with Pelmora, you won’t regret it” Miles Carter, CEO, TBA | “Pelmora is the best kept secret on the internet for converting more prospects to customers. I don’t know where my business would be today without it</p>
  <p class="abs t-name">MILES CARTER</p>
  <p class="abs t-role">CEO, TBA</p>
  <span class="abs t-nav" style="left:767px"></span>
  <span class="abs t-nav" style="left:779px"></span>

  <footer class="abs footer"></footer>
  <p class="abs f-links">Home &nbsp;/ &nbsp;Projects &nbsp;/ &nbsp;How it works &nbsp;/ &nbsp;Plans &nbsp;/ &nbsp;My Account</p>
  <p class="abs f-copy">Copyright © 2015 pelmora – All Rights Reserved</p>
  <div class="abs social"><i></i><i></i><i></i><i></i><i></i></div>

</div>
</body>
</html>
```